Veranix - Solution provider in business consulting

Veranix is a swiss based company providing solutions for developing markets. The business covers various fields of business consulting, such as supply chain, product costs, quality management and manufacturing management. The Business operates in a efficient, straight and solution oriented manner.
The final design should communicate these characteristics. Asian people as well as as western people shall identify the qualities of the company at first sight.
The customer needs business cards with a simple view but an recognizable design, printed in high quality. Engraved elements such as the globe or simple words are possible.
Available colors are: (RAL)
102/102/102
51/102/102
153/204/153
255/102/51
Font: Calibri

```html
<!DOCTYPE html>
<html lang="en">
<head>
<meta charset="utf-8">
<title>Veranix – Business Card</title>
<link rel="stylesheet" href="https://fonts.googleapis.com/css2?family=Carlito:wght@400;700&display=swap">
<style>
  :root {
    --page-bg: #e9e7e3;
    --card-white: #ffffff;
    --graphite: #666666;
    --graphite-dark: #4a4a4a;
    --graphite-deep: #3a3a3a;
    --graphite-light: #7a7a7a;
    --ink-light: #f2f2f2;
    --ink-soft: #d9d9d9;
    --mark-fill: #cfcfcf;
    --shadow: rgba(0,0,0,0.25);
  }
  * { box-sizing: border-box; margin: 0; padding: 0; }
  html, body {
    width: 1200px; height: 950px; overflow: hidden;
    background: var(--page-bg);
    font-family: "Carlito", Calibri, Arial, sans-serif;
  }
  .sheet {
    width: 1200px; height: 950px;
    display: flex; flex-direction: column;
    align-items: center; justify-content: center; gap: 56px;
  }
  .card {
    width: 620px; height: 400px;
    border-radius: 4px;
    box-shadow: 0 14px 30px var(--shadow);
    overflow: hidden;
    position: relative;
  }

  /* Front */
  .card--front { display: flex; }
  .front-brand {
    width: 56%; background: var(--card-white);
    display: flex; align-items: center; justify-content: center;
  }
  .brand-name {
    font-size: 66px; font-weight: 400; color: var(--graphite);
    letter-spacing: 1px; line-height: 1;
  }
  .front-info {
    width: 44%; position: relative;
    background: linear-gradient(100deg, var(--graphite-light) 0%, var(--graphite) 18%, var(--graphite-dark) 100%);
    color: var(--ink-light);
    padding: 54px 26px 0 40px;
  }
  .front-info::before {
    content: ""; position: absolute; left: 0; top: 0; bottom: 0; width: 28px;
    background: linear-gradient(90deg, rgba(255,255,255,0.16), rgba(255,255,255,0));
  }
  .person-name { font-size: 22px; font-weight: 700; line-height: 1.1; }
  .person-role { font-size: 13px; color: var(--ink-soft); margin-top: 3px; }
  .company { margin-top: 30px; font-size: 15px; line-height: 1.3; }
  .company-name { font-weight: 700; }
  .contact-list { list-style: none; margin-top: 18px; font-size: 15px; line-height: 1.45; }
  .contact-list li { display: flex; align-items: center; gap: 8px; }
  .contact-list svg { width: 13px; height: 13px; flex: none; fill: var(--ink-light); }

  /* Back */
  .card--back {
    background: linear-gradient(100deg, var(--graphite-light) 0%, var(--graphite) 45%, var(--graphite-deep) 100%);
    display: flex; flex-direction: column; align-items: center; justify-content: center; gap: 22px;
  }
  .back-dot { width: 120px; height: 120px; border-radius: 50%; background: var(--mark-fill); }
  .back-url { font-size: 22px; color: var(--ink-soft); letter-spacing: 3px; }
</style>
</head>
<body>
<main class="sheet">

  <section class="card card--front" aria-label="Business card front">
    <div class="front-brand">
      <span class="brand-name">veranix</span>
    </div>
    <div class="front-info">
      <p class="person-name">Marco Vettel</p>
      <p class="person-role">CEO</p>
      <div class="company">
        <p class="company-name">Veranix GmbH</p>
        <p>Talweg 18, 9230 Lindau</p>
        <p>Switzerland</p>
      </div>
      <ul class="contact-list">
        <li>
          <svg viewBox="0 0 16 16" aria-hidden="true"><path d="M2 5c0-2 2-3 6-3s6 1 6 3v1h-3V5H5v1H2zM3 7h10l1 7H2z"/></svg>
          +41 71 555 0142
        </li>
        <li>
          <svg viewBox="0 0 16 16" aria-hidden="true"><path d="M4 1h8v14H4zM5.5 3v9h5V3z"/></svg>
          +41 79 555 0187
        </li>
        <li>
          <svg viewBox="0 0 16 16" aria-hidden="true"><path d="M1 3h14v10H1zM2 4l6 5 6-5v-0.01z" fill-rule="evenodd"/></svg>
          marco.vettel@veranix.ch
        </li>
        <li>
          <svg viewBox="0 0 16 16" aria-hidden="true"><circle cx="8" cy="8" r="7"/></svg>
          www.veranix.ch
        </li>
      </ul>
    </div>
  </section>

  <section class="card card--back" aria-label="Business card back">
    <div class="back-dot"></div>
    <p class="back-url">veranix.ch</p>
  </section>

</main>
</body>
</html>
```